Harbor Crestline (Business Card Design)

Need business cards designed. Something modern, chic, and sleek. Mabye the back of the card should be the navy blue that is in the logo and then just the logo on the back.

Target Market(s)

Those in the hotel, office, and renovation industry

Contact Information for Business Card

1. Logo 2. Dorian Fenwick 3. CEO/Founder 4. Phone: (833) HarbCre / (833) 427-2731 5. Email: dorian@theharborcrestline.com 6. Website: www.theharborcrestline.com

Font styles to use
Other font styles liked:
• Look at the logo font and base the font for everything else off of that.

Colors
0054AA
0677BA
7BADD7
CADEEF
E8F1F8

Requirements
Must have
• Colors that are associated in the logo
Nice to have
• Sleek modern clean and chic design.

```html
<!DOCTYPE html>
<html lang="en">
<head>
<meta charset="utf-8">
<title>Harbor Crestline — Business Card</title>
<link rel="stylesheet" href="https://fonts.googleapis.com/css2?family=Montserrat:wght@500&family=Poppins:wght@400;500;700&display=swap">
<style>
  :root {
    --navy-core: #0d2268;
    --navy-deep: #040c2e;
    --gold: #c9a14a;
    --ink: #1a1a2a;
    --rule: #1b2a78;
    --paper: #ffffff;
    --mist: #e4e4e6;
    --page: #ffffff;
    --line: rgba(255,255,255,0.08);
  }
  * { margin: 0; padding: 0; box-sizing: border-box; }
  html, body {
    width: 800px; height: 1200px; overflow: hidden;
    background: var(--page);
  }
  .sheet {
    position: relative; width: 800px; height: 1200px;
  }
  .card {
    position: absolute; left: 100px;
    width: 600px; height: 343px;
    overflow: hidden;
    box-shadow: 0 4px 14px rgba(0,0,0,0.18);
  }
  .card--front { top: 210px; }
  .card--back { top: 640px; background: var(--paper); }
  .card__art {
    position: absolute; inset: 0; width: 100%; height: 100%;
  }
  .wordmark {
    position: absolute;
    display: flex; flex-direction: column; align-items: center;
    font-family: "Montserrat", sans-serif; font-weight: 500;
    color: #ffffff; text-transform: uppercase; text-align: center;
  }
  .wordmark__square {
    width: 10px; height: 10px; background: var(--gold); margin-bottom: 14px;
  }
  .wordmark__text { letter-spacing: 0.12em; line-height: 1.15; }
  .card--front .wordmark {
    left: 0; width: 600px; top: 112px;
  }
  .card--front .wordmark__text { font-size: 30px; }
  .card--back .wordmark {
    left: 0; width: 254px; top: 118px;
  }
  .card--back .wordmark__text { font-size: 20px; }

  .contact {
    position: absolute; left: 341px; top: 96px;
    font-family: "Poppins", sans-serif;
  }
  .contact__name {
    font-weight: 700; font-size: 24px; color: var(--gold);
    line-height: 1; letter-spacing: 0.01em;
  }
  .contact__role {
    font-weight: 500; font-size: 13px; color: var(--ink);
    margin-top: 4px;
  }
  .contact__rule {
    width: 46px; height: 1px; background: var(--rule); margin-top: 5px;
  }
  .contact__list { list-style: none; margin-top: 12px; }
  .contact__item {
    display: flex; align-items: center; gap: 5px;
    height: 27px; color: var(--ink);
    font-size: 13.5px;
  }
  .contact__item--small { font-size: 11.5px; }
  .contact__icon { width: 22px; height: 22px; flex: none; }
</style>
</head>
<body>
<main class="sheet">

  <section class="card card--front" aria-label="Card front">
    <svg class="card__art" viewBox="0 0 922 527" preserveAspectRatio="none" aria-hidden="true">
      <defs>
        <radialGradient id="frontGlow" cx="50%" cy="50%" r="60%">
          <stop offset="0" stop-color="#0d2470"/>
          <stop offset="0.55" stop-color="#081a55"/>
          <stop offset="1" stop-color="#030a2a"/>
        </radialGradient>
      </defs>
      <rect width="922" height="527" fill="url(#frontGlow)"/>
      <g fill="none" stroke="var(--line)" stroke-width="1.2">
        <polygon points="461,0 745,264 461,527 177,264"/>
        <line x1="440" y1="0" x2="0" y2="420"/>
        <line x1="482" y1="0" x2="922" y2="420"/>
        <line x1="440" y1="527" x2="0" y2="107"/>
        <line x1="482" y1="527" x2="922" y2="107"/>
      </g>
    </svg>
    <div class="wordmark">
      <span class="wordmark__square"></span>
      <span class="wordmark__text">Harbor<br>Crestline</span>
    </div>
  </section>

  <section class="card card--back" aria-label="Card back">
    <svg class="card__art" viewBox="0 0 922 527" preserveAspectRatio="none" aria-hidden="true">
      <defs>
        <radialGradient id="backGlow" cx="30%" cy="50%" r="55%">
          <stop offset="0" stop-color="#0d2470"/>
          <stop offset="0.6" stop-color="#081a55"/>
          <stop offset="1" stop-color="#040c30"/>
        </radialGradient>
      </defs>
      <rect width="922" height="527" fill="var(--paper)"/>
      <polygon points="250,0 475,0 290,263 475,527 250,527" fill="var(--mist)"/>
      <polygon points="0,0 250,0 512,263 250,527 0,527" fill="url(#backGlow)"/>
      <g fill="none" stroke="var(--line)" stroke-width="1.2">
        <polygon points="196,0 455,263 196,527 -63,263"/>
      </g>
    </svg>
    <div class="wordmark">
      <span class="wordmark__square"></span>
      <span class="wordmark__text">Harbor<br>Crestline</span>
    </div>

    <div class="contact">
      <h1 class="contact__name">DORIAN FENWICK</h1>
      <p class="contact__role">CEO/Founder</p>
      <div class="contact__rule"></div>
      <ul class="contact__list">
        <li class="contact__item">
          <svg class="contact__icon" viewBox="0 0 22 22" aria-hidden="true">
            <rect x="4" y="4" width="14" height="14" transform="rotate(45 11 11)" fill="var(--navy-core)"/>
            <path d="M8 8.5c0.5 2.8 2.7 5 5.5 5.5l1-1.3-1.6-1-0.8 0.7c-1-0.5-1.8-1.3-2.3-2.3l0.7-0.8-1-1.6z" fill="var(--gold)"/>
          </svg>
          <span>(833) HarbCre</span>
        </li>
        <li class="contact__item">
          <svg class="contact__icon" viewBox="0 0 22 22" aria-hidden="true">
            <rect x="4" y="4" width="14" height="14" transform="rotate(45 11 11)" fill="var(--navy-core)"/>
            <path d="M8 8.5c0.5 2.8 2.7 5 5.5 5.5l1-1.3-1.6-1-0.8 0.7c-1-0.5-1.8-1.3-2.3-2.3l0.7-0.8-1-1.6z" fill="var(--gold)"/>
          </svg>
          <span>(833) 427-2731</span>
        </li>
        <li class="contact__item contact__item--small">
          <svg class="contact__icon" viewBox="0 0 22 22" aria-hidden="true">
            <rect x="4" y="4" width="14" height="14" transform="rotate(45 11 11)" fill="var(--navy-core)"/>
            <rect x="7.5" y="8.5" width="7" height="5" fill="var(--gold)"/>
            <path d="M7.5 8.5l3.5 2.6 3.5-2.6" fill="none" stroke="var(--navy-core)" stroke-width="0.7"/>
          </svg>
          <span>dorian@theharborcrestline.com</span>
        </li>
        <li class="contact__item contact__item--small">
          <svg class="contact__icon" viewBox="0 0 22 22" aria-hidden="true">
            <rect x="4" y="4" width="14" height="14" transform="rotate(45 11 11)" fill="var(--navy-core)"/>
            <circle cx="11" cy="11" r="3.6" fill="none" stroke="var(--gold)" stroke-width="0.9"/>
            <path d="M7.4 11h7.2M11 7.4v7.2" stroke="var(--gold)" stroke-width="0.7"/>
          </svg>
          <span>www.theharborcrestline.com</span>
        </li>
      </ul>
    </div>
  </section>

</main>
</body>
</html>
```